Adult dating site banners and payment page concepts

We need an overhaul done on our banners, as well as rebranding our packages. We have uploaded a full description of what we need doing, we are not looking for you do do all of them right now. We are looking for a concept for one site banner, one version of the payment page, and one affiliate banner. We will then pay the winner to do the rest of the design work we need to get them all done, but we have uploaded all the bits we will eventually need.

Colors

Designer to choose colors to be used in the design.

Requirements
Must have
• Banner design brief
• We are looking for a new design for all of our upgrade banners for our adult dating swingers sites as well as our payment pages so they need to appeal to men, women, and couples. We are looking for something fun and sexy that really looks nice on mobile and desktop.
• Important design notes banners
• 1. Where you see the word “Extras” we are changing it to a package called “Plus, this can be the word Plus or the + symbol, or both”, we are looking for a design for this.
• 2. Where you see the word “Premium” we are now calling it “Supporter” so that needs some nice font or design as well.
• 3. We would like the offers to jump out at you with the discounts etc.
• 4. The banners need to be able to work on our different sites on the following colours:
• South Africa #7e0202
• UK #0d72ba
• Canada #147eab
• Ireland #003a15
• Australia #272f47
• New Zealand #446160
• Payment pages
• 1. We would like to keep them clean as most of our users are on mobile
• 2. But if you think they can be improved to help with conversion rates we would like to see it.
• Affiliate banners
• We also advertise our sites on other websites using geo-targeted banners; we need to tempt people to click through. The ones we have right now are not animated and we like the idea of that, something saucy and sexy but not porn related. We would like these to be re designed to be something sexier that grabs your attention.

```html
<!DOCTYPE html>
<html lang="en">
<head>
<meta charset="utf-8">
<title>Upgrade Now – Payment Plan</title>
<link href="https://fonts.googleapis.com/css2?family=Lato:wght@400;700&display=swap" rel="stylesheet">
<style>
  :root {
    --page-bg: #e9ebef;
    --card-bg: #ffffff;
    --heading-red: #8e1b1b;
    --supporter-blue: #4196c6;
    --plus-green: #3ab14b;
    --tick-green: #2e7d3a;
    --text-dark: #222222;
    --row-alt: #f5f5f5;
    --line: #d9d9d9;
    --close-grey: #555555;
  }
  * { box-sizing: border-box; margin: 0; padding: 0; }
  html, body { width: 1200px; height: 1200px; overflow: hidden; }
  body {
    background: var(--page-bg);
    font-family: "Lato", Arial, sans-serif;
    color: var(--text-dark);
    position: relative;
  }
  .upgrade-modal {
    position: absolute;
    left: 372px; top: 102px;
    width: 456px; height: 996px;
    background: var(--card-bg);
    overflow: hidden;
  }
  .close-button {
    position: absolute; right: 20px; top: 16px;
    width: 28px; height: 28px;
  }
  .modal-title {
    position: absolute; top: 34px; left: 0; right: 0;
    text-align: center; font-size: 31px; font-weight: 400;
    color: var(--heading-red);
  }
  .plan-label {
    position: absolute; top: 98px; left: 0; right: 0;
    text-align: center; font-size: 25px; color: var(--heading-red);
  }
  .billing-toggle {
    position: absolute; left: 71px; top: 140px;
    width: 319px; height: 47px;
    display: flex; border: 1px solid #c9c9c9; border-radius: 3px; overflow: hidden;
  }
  .billing-toggle span {
    flex: 1; display: flex; align-items: center; justify-content: center;
    font-size: 23px;
  }
  .billing-toggle .is-active { background: var(--plus-green); color: #fff; }
  .plan-card {
    position: absolute; top: 211px; width: 196px; height: 145px;
    color: #fff; text-align: center; border-radius: 3px;
    box-shadow: 0 2px 4px rgba(0,0,0,0.25);
  }
  .plan-card.supporter { left: 28px; background: var(--supporter-blue); }
  .plan-card.plus { left: 235px; background: var(--plus-green); }
  .plan-name { margin-top: 16px; font-size: 25px; }
  .plan-price { margin-top: 2px; font-size: 41px; line-height: 1.1; }
  .plan-period { margin-top: 12px; font-size: 18px; }
  .feature-table {
    position: absolute; left: 23px; top: 361px; width: 413px;
    list-style: none;
  }
  .feature-row {
    height: 64px; display: flex; align-items: center; font-size: 18px;
  }
  .feature-row:nth-child(even) { background: var(--row-alt); }
  .feature-row .mark {
    width: 72px; text-align: center; font-weight: 700; font-size: 18px;
    display: flex; justify-content: center;
  }
  .feature-row .feature-name { flex: 1; text-align: center; white-space: nowrap; }
  .feature-row .tick { width: 19px; height: 16px; }
  .modal-footer {
    position: absolute; left: 0; top: 931px; width: 100%; height: 65px;
    background: var(--card-bg); border-top: 1px solid var(--line);
  }
  .upgrade-button {
    position: absolute; top: 7px; width: 204px; height: 54px;
    color: #fff; font-size: 25px; border-radius: 3px;
    display: flex; align-items: center; justify-content: center;
  }
  .upgrade-button.supporter { left: 20px; background: var(--supporter-blue); }
  .upgrade-button.plus { left: 235px; background: var(--plus-green); }
</style>
</head>
<body>
<svg width="0" height="0" style="position:absolute">
  <symbol id="tick" viewBox="0 0 19 16">
    <path d="M2 8.5 L7 13.5 L17 2.5" fill="none" stroke="var(--tick-green)" stroke-width="3.2" stroke-linecap="round" stroke-linejoin="round"/>
  </symbol>
</svg>

<section class="upgrade-modal">
  <svg class="close-button" viewBox="0 0 28 28" aria-label="Close">
    <path d="M7 7 L21 21 M21 7 L7 21" stroke="var(--close-grey)" stroke-width="3.5" stroke-linecap="round"/>
  </svg>
  <h1 class="modal-title">Upgrade Now</h1>
  <h2 class="plan-label" style="font-weight:400">Payment plan</h2>
  <div class="billing-toggle">
    <span class="is-active">Monthly</span>
    <span>Yearly</span>
  </div>

  <div class="plan-card supporter">
    <div class="plan-name">Supporter</div>
    <div class="plan-price">R134,95</div>
    <div class="plan-period">monthly</div>
  </div>
  <div class="plan-card plus">
    <div class="plan-name">Plus</div>
    <div class="plan-price">R154,95</div>
    <div class="plan-period">monthly</div>
  </div>

  <ul class="feature-table">
    <li class="feature-row"><span class="mark"><svg class="tick"><use href="#tick"/></svg></span><span class="feature-name">Cancel at any time</span><span class="mark"><svg class="tick"><use href="#tick"/></svg></span></li>
    <li class="feature-row"><span class="mark"><svg class="tick"><use href="#tick"/></svg></span><span class="feature-name">Unlimited Messaging</span><span class="mark"><svg class="tick"><use href="#tick"/></svg></span></li>
    <li class="feature-row"><span class="mark"><svg class="tick"><use href="#tick"/></svg></span><span class="feature-name">Adult Photos and Videos</span><span class="mark"><svg class="tick"><use href="#tick"/></svg></span></li>
    <li class="feature-row"><span class="mark"><svg class="tick"><use href="#tick"/></svg></span><span class="feature-name">Full Chatroom Access</span><span class="mark"><svg class="tick"><use href="#tick"/></svg></span></li>
    <li class="feature-row"><span class="mark" style="width:58px"><svg class="tick"><use href="#tick"/></svg></span><span class="feature-name">Send Statuses to Friends &amp; Followers</span><span class="mark" style="width:58px"><svg class="tick"><use href="#tick"/></svg></span></li>
    <li class="feature-row"><span class="mark">2</span><span class="feature-name">Chatroom Webcams</span><span class="mark">7</span></li>
    <li class="feature-row"><span class="mark">-</span><span class="feature-name">Send Statuses to Matches</span><span class="mark"><svg class="tick"><use href="#tick"/></svg></span></li>
    <li class="feature-row"><span class="mark">-</span><span class="feature-name">Multiple Chat Access for Couples</span><span class="mark"><svg class="tick"><use href="#tick"/></svg></span></li>
    <li class="feature-row"><span class="mark">-</span><span class="feature-name">HD Photos and Videos</span><span class="mark"><svg class="tick"><use href="#tick"/></svg></span></li>
  </ul>

  <div class="modal-footer">
    <span class="upgrade-button supporter">Upgrade Now</span>
    <span class="upgrade-button plus">Upgrade Now</span>
  </div>
</section>
</body>
</html>
```